Business Card for beauty technology startup

Design Glimora Business Card for a Beauty, based on the website identity and colors (https://www.glimora-example.com).
Glimora is a beauty tech startup that gathers helpful product info for beauty lovers and consumers (such as availability on stores, price range and product reviews) for makeup products. The card design must be young, colorful but clean, and very modern.

Target Market(s)

woman, 15-35

Industry/Entity Type

Cosmetics

Contact Information for Business Card

Full Name, address, phone

Font styles to use
Other font styles liked:
• Advent Pro

Colors
e34297
86cfc6
ffffff
5c5c5c
e8e8e8
e667a6
b2b2b2

Requirements
Must have
• One full colored side with a creative design and another with card info
• Use Color palette: #95C5C5 and/or #D38AA5
• Use fonts: Advent Pro
• Use website identity: https://www.glimora-example.com
Nice to have
• If needed extra font: Roboto

```html
<!DOCTYPE html>
<html lang="en">
<head>
<meta charset="utf-8">
<title>Glimora Business Card</title>
<link href="https://fonts.googleapis.com/css2?family=Advent+Pro:wght@300;400&family=Roboto:wght@400;500&display=swap" rel="stylesheet">
<style>
  :root {
    --backdrop: #e9e6e2;
    --paper: #f6f6f5;
    --mauve: #a8738a;
    --mauve-soft: #b07b91;
    --ink-dark: #17181a;
    --edge-grey: #b2b2b2;
    --text-light: #ffffff;
  }
  * { margin: 0; padding: 0; box-sizing: border-box; }
  html, body {
    width: 1200px; height: 960px; overflow: hidden;
    background: var(--backdrop);
  }
  .canvas { position: relative; width: 1200px; height: 960px; }

  .card {
    position: absolute; width: 600px; height: 343px;
    border-radius: 18px; overflow: hidden;
  }

  /* Info side */
  .card-front { left: 314px; top: 113px; background: var(--mauve); }
  .card-front .split { position: absolute; inset: 0; }
  .brand-ring {
    position: absolute; left: 16px; top: 30px;
    width: 260px; height: 260px; border-radius: 50%;
    border: 4px solid var(--mauve);
  }
  .brand-name-front {
    position: absolute; left: 16px; top: 30px; width: 260px; height: 260px;
    display: flex; align-items: center; justify-content: center;
    font-family: "Advent Pro", sans-serif; font-weight: 400;
    font-size: 54px; letter-spacing: 3px; color: var(--mauve);
  }
  .contact {
    position: absolute; right: 29px;
    text-align: right; color: var(--text-light);
    font-family: "Roboto", sans-serif;
  }
  .contact-name { top: 36px; font-size: 19px; font-weight: 500; line-height: 24px; }
  .contact-title { top: 61px; font-size: 14px; font-weight: 400; line-height: 18px; }
  .contact-address { top: 186px; font-size: 13.5px; line-height: 19px; }
  .contact-lines { top: 237px; right: 29px; font-size: 13.5px; line-height: 19.7px; }
  .contact-line { display: flex; justify-content: flex-end; align-items: center; gap: 9px; }
  .contact-line svg { width: 13px; height: 13px; flex: none; }

  /* Brand side */
  .card-back { left: 311px; top: 473px; background: var(--ink-dark); }
  .brand-dot {
    position: absolute; left: 250px; top: 78px;
    width: 100px; height: 100px; border-radius: 50%;
    border: 3px solid var(--mauve-soft);
  }
  .brand-name-back {
    position: absolute; left: 0; right: 0; top: 205px; text-align: center;
    font-family: "Advent Pro", sans-serif; font-weight: 300;
    font-size: 46px; letter-spacing: 7px; color: var(--mauve-soft);
  }
  .brand-url {
    position: absolute; left: 0; right: 0; top: 294px; text-align: center;
    font-family: "Roboto", sans-serif; font-size: 13.5px;
    letter-spacing: 4.5px; color: var(--text-light);
  }
</style>
</head>
<body>
<main class="canvas">

  <section class="card card-front" aria-label="Card info side">
    <svg class="split" viewBox="0 0 600 343" width="600" height="343" aria-hidden="true">
      <path d="M0 0 H272 Q345 172 246 343 H0 Z" fill="var(--edge-grey)"/>
      <path d="M0 0 H266 Q335 172 238 343 H0 Z" fill="var(--paper)"/>
    </svg>
    <div class="brand-ring" aria-hidden="true"></div>
    <div class="brand-name-front">Glimora</div>

    <div class="contact contact-name">MAYA LINDEN</div>
    <div class="contact contact-title">CEO/FOUNDER</div>
    <div class="contact contact-address">4210 Willowmere Road<br>Fairbrook, Oregon 97811</div>

    <div class="contact contact-lines">
      <div class="contact-line">555 210 4381
        <svg viewBox="0 0 24 24" aria-label="Phone"><path fill="#fff" d="M6.6 10.8a15 15 0 0 0 6.6 6.6l2.2-2.2a1 1 0 0 1 1-.25 11.4 11.4 0 0 0 3.6.57 1 1 0 0 1 1 1V20a1 1 0 0 1-1 1A17 17 0 0 1 3 4a1 1 0 0 1 1-1h3.5a1 1 0 0 1 1 1c0 1.25.2 2.45.57 3.57a1 1 0 0 1-.25 1z"/></svg>
      </div>
      <div class="contact-line">555 318 7702
        <svg viewBox="0 0 24 24" aria-label="Mobile"><rect x="6" y="2" width="12" height="20" rx="2" fill="none" stroke="#fff" stroke-width="2"/><circle cx="12" cy="18" r="1.2" fill="#fff"/></svg>
      </div>
      <div class="contact-line">555 462 0915
        <svg viewBox="0 0 24 24" aria-label="Fax"><rect x="6" y="3" width="12" height="6" fill="#fff"/><rect x="3" y="10" width="18" height="8" rx="1.5" fill="#fff"/><rect x="7" y="15" width="10" height="6" fill="#fff" stroke="var(--mauve)" stroke-width="1.5"/></svg>
      </div>
      <div class="contact-line">info@glimora-example.com
        <svg viewBox="0 0 24 24" aria-label="Email"><rect x="2" y="5" width="20" height="14" rx="1.5" fill="#fff"/><path d="M2.5 6 L12 13 L21.5 6" fill="none" stroke="var(--mauve)" stroke-width="1.6"/></svg>
      </div>
    </div>
  </section>

  <section class="card card-back" aria-label="Card brand side">
    <div class="brand-dot" aria-hidden="true"></div>
    <div class="brand-name-back">GLIMORA</div>
    <div class="brand-url">www.glimora-example.com</div>
  </section>

</main>
</body>
</html>
```